Business Card Design Project

We need a business card for a new technology services company. We develop software and implement software packages for our business customers and although we will begin with just one or two service offerings, our service offerings will expand over time. Our name comes from the an author, KL Barrow, and his "idea" was that opportunity should be based on ability and achievement, not on social status.

We would like to see a design that is standard in its size and shape, but stands apart in its dramatic color contrasts. The card should not use too many colors - the colors used in the background should highlight the brilliant blues of the logo (see attachment) to dramatic effect. The background should not be white.

If necessary, you can change the color of the words "KL Barrow", but not the word "Idea".

Card size should be U.S. standard 2 inches by 3.5 inches and provide for 1/8 inch bleed area on each side.

We need a design for both sides of the business card, one side communicating the company logo and contact information, the other side being purely graphical, incorporating the logo but no other information.

Contact Information Required:
Kate Brook
KateBrook@klbarrowvista.com
614-387-2259

Target Market(s)

Business executives

Industry/Entity Type

Software

Requirements
Must have
• It must have the full company logo on one side, and at least the graphic element of the logo on the other. Either that or the full logo on both.
Nice to have
• It would be nice to have a design that could work without needing two different textures. For example, it would be nice if the entire card could be shiny, not just parts of the card.

It would also be nice if texture is something we could add later.
Should not have
• The card should not use the color green.

```html
<!DOCTYPE html>
<html lang="en">
<head>
<meta charset="utf-8">
<title>KL Barrow Vista – Business Cards</title>
<link rel="stylesheet" href="https://fonts.googleapis.com/css2?family=Roboto:wght@300;400;700&display=swap">
<style>
  :root {
    --page-bg: #e6e6ea;
    --card-dark: #1b1b1c;
    --card-dark-2: #2c2c2e;
    --brand-blue: #0aa2e3;
    --brand-blue-deep: #0588c8;
    --stripe-grey: #b9babc;
    --logo-grey: #c9cacc;
    --text-white: #ffffff;
    --text-soft: #e4e4e4;
  }
  html, body {
    margin: 0;
    padding: 0;
    width: 1200px;
    height: 987px;
    overflow: hidden;
    background: var(--page-bg);
    font-family: "Roboto", Arial, sans-serif;
  }
  .sheet {
    position: relative;
    width: 1200px;
    height: 987px;
  }
  .card {
    position: absolute;
    width: 640px;
    height: 366px;
    border-radius: 22px;
    overflow: hidden;
    background: linear-gradient(135deg, var(--card-dark-2) 0%, var(--card-dark) 55%, #121213 100%);
    box-shadow: 0 10px 30px rgba(0,0,0,0.18);
  }
  .card-back { left: 520px; top: 50px; }
  .card-front { left: 40px; top: 560px; }

  .wordmark {
    position: absolute;
    display: flex;
    align-items: center;
    gap: 18px;
    color: var(--logo-grey);
    font-weight: 300;
    letter-spacing: -1px;
    white-space: nowrap;
  }
  .wordmark-dot {
    display: block;
    border-radius: 50%;
    background: var(--brand-blue);
  }
  .card-back .wordmark { left: 40px; top: 150px; font-size: 50px; }
  .card-back .wordmark-dot { width: 56px; height: 56px; }

  .front-sweep {
    position: absolute;
    inset: 0;
  }
  .card-front .wordmark { left: 36px; top: 128px; font-size: 36px; }
  .card-front .wordmark-dot { width: 40px; height: 40px; }

  .holder-name {
    position: absolute;
    right: 36px;
    top: 108px;
    color: var(--text-white);
    font-weight: 700;
    font-size: 26px;
    line-height: 30px;
    letter-spacing: 1px;
    text-transform: uppercase;
    white-space: nowrap;
  }
  .contact-list {
    position: absolute;
    left: 36px;
    top: 196px;
    margin: 0;
    padding: 0;
    list-style: none;
    color: var(--text-soft);
    font-size: 16px;
    font-weight: 400;
  }
  .contact-list li {
    display: flex;
    align-items: center;
    gap: 8px;
    margin-bottom: 10px;
  }
  .contact-icon { width: 14px; height: 14px; flex: none; }
</style>
</head>
<body>
<main class="sheet">

  <section class="card card-back" aria-label="Card back">
    <div class="wordmark">
      <span class="wordmark-name">KL Barrow Vista</span>
      <span class="wordmark-dot"></span>
    </div>
  </section>

  <section class="card card-front" aria-label="Card front">
    <svg class="front-sweep" viewBox="0 0 640 366" width="640" height="366" aria-hidden="true">
      <defs>
        <linearGradient id="sweepBlue" x1="0" y1="0" x2="1" y2="1">
          <stop offset="0" stop-color="var(--brand-blue)"/>
          <stop offset="1" stop-color="var(--brand-blue-deep)"/>
        </linearGradient>
      </defs>
      <path d="M0,0 H640 V366 H548 C510,210 380,70 0,42 Z" fill="var(--stripe-grey)"/>
      <path d="M0,0 H640 V366 H572 C535,200 400,55 0,26 Z" fill="url(#sweepBlue)"/>
      <path d="M0,50 C330,72 470,150 530,262" fill="none" stroke="#0c0c0d" stroke-width="3"/>
    </svg>

    <div class="wordmark">
      <span class="wordmark-name">KL Barrow Vista</span>
      <span class="wordmark-dot"></span>
    </div>

    <ul class="contact-list">
      <li>
        <svg class="contact-icon" viewBox="0 0 16 16" aria-hidden="true">
          <circle cx="8" cy="8" r="8" fill="var(--brand-blue)"/>
          <path d="M5 4.5 L6.6 4.3 L7.3 6.2 L6.4 7 C6.9 8 7.8 8.9 8.9 9.5 L9.7 8.6 L11.6 9.3 L11.4 10.9 C8 11 5 8 5 4.5 Z" fill="#fff"/>
        </svg>
        <span>614-387-2259</span>
      </li>
      <li>
        <svg class="contact-icon" viewBox="0 0 16 16" aria-hidden="true">
          <circle cx="8" cy="8" r="8" fill="var(--brand-blue)"/>
          <rect x="3.8" y="5" width="8.4" height="6" fill="#fff"/>
          <path d="M3.8 5 L8 8.4 L12.2 5" fill="none" stroke="var(--brand-blue)" stroke-width="1"/>
        </svg>
        <span>KateBrook@klbarrowvista.com</span>
      </li>
    </ul>

    <div class="holder-name">Kate Brook</div>
  </section>

</main>
</body>
</html>
```